business card for a massage therapy practice named 'Cedar and Willow Massage Studio'

I really need a trendy, yet easy on the eyes business card to complement my logo. Ideally with some gold or rose gold foil work.

My uploaded file of the logo I have in horizontal but I have a vertical version as well. Another color that is used in the website is a blush pink here and there. I'd like to see some trendy tropical leaves in the design.

```html
<!DOCTYPE html>
<html lang="en">
<head>
<meta charset="utf-8">
<title>Cedar and Willow Massage Studio – Business Card</title>
<link rel="stylesheet" href="https://fonts.googleapis.com/css2?family=Open+Sans:wght@400;600&family=Kaushan+Script&display=swap">
<style>
  :root {
    --backdrop: #2b2b2c;
    --card: #1d1e20;
    --pattern-light: #34353a;
    --pattern-mid: #2a2b2f;
    --ink-white: #f2f2f2;
    --ink-soft: #d6d6d6;
    --teal: #7fd6bd;
    --gold: #a88d5a;
    --rule: #5a5b5e;
  }
  * { box-sizing: border-box; margin: 0; padding: 0; }
  html, body {
    width: 1200px;
    height: 1108px;
    overflow: hidden;
    background: var(--backdrop);
  }
  .canvas { position: relative; width: 1200px; height: 1108px; }

  .card {
    position: absolute;
    top: 204px;
    width: 400px;
    height: 700px;
    border-radius: 20px;
    background: var(--card);
    overflow: hidden;
    box-shadow: 0 14px 30px rgba(0,0,0,0.35);
  }
  .card--front { left: 160px; }
  .card--back { left: 640px; }

  .brand {
    position: absolute;
    left: 0;
    right: 0;
    display: flex;
    align-items: center;
    justify-content: center;
    gap: 16px;
    font-family: "Open Sans", sans-serif;
    font-weight: 600;
    color: var(--ink-white);
  }
  .brand__mark {
    flex: none;
    width: 44px;
    height: 44px;
    border-radius: 50%;
    background: var(--gold);
  }
  .brand__text { text-align: left; line-height: 1.3; }
  .brand__name { display: block; font-size: 30px; letter-spacing: 0.02em; }
  .brand__tag { display: block; font-size: 15px; letter-spacing: 0.3em; }
  .card--front .brand { top: 130px; }
  .card--back .brand { top: 560px; }
  .card--back .brand__text { text-align: center; }

  .contact {
    position: absolute;
    top: 330px;
    left: 60px;
    right: 60px;
    text-align: center;
    font-family: "Open Sans", sans-serif;
    color: var(--ink-soft);
    font-size: 17px;
    line-height: 1.45;
  }
  .contact__name {
    font-family: "Kaushan Script", cursive;
    color: var(--teal);
    font-size: 38px;
    line-height: 1.2;
    margin-bottom: 4px;
  }
  .contact__rule {
    height: 1px;
    background: var(--rule);
    margin: 12px 10px;
  }

  .pattern {
    position: absolute;
    top: 0;
    left: 0;
    right: 0;
    height: 540px;
    background:
      radial-gradient(ellipse at 70% 20%, var(--pattern-light) 0%, transparent 60%),
      radial-gradient(ellipse at 25% 55%, var(--pattern-mid) 0%, transparent 65%),
      linear-gradient(180deg, var(--pattern-mid) 0%, var(--card) 100%);
  }
</style>
</head>
<body>
<div class="canvas">
  <section class="card card--front">
    <div class="brand">
      <span class="brand__mark"></span>
      <span class="brand__text">
        <span class="brand__name">Cedar &amp; Willow</span>
        <span class="brand__tag">MASSAGE STUDIO</span>
      </span>
    </div>
    <div class="contact">
      <p class="contact__name">Marisol Vega</p>
      <p class="contact__role">Massage Therapist</p>
      <div class="contact__rule"></div>
      <p>482 Linden Ave. suite 210</p>
      <p>Riverton, CA 95000</p>
      <div class="contact__rule"></div>
      <p>(555) 014-2287</p>
      <p>cedarandwillow@mail.com</p>
    </div>
  </section>

  <section class="card card--back">
    <div class="pattern" role="img" aria-label="Faint repeating tropical fruit pattern in dark grey tones across the card"></div>
    <div class="brand">
      <span class="brand__text">
        <span class="brand__name">Cedar &amp; Willow</span>
        <span class="brand__tag">MASSAGE STUDIO</span>
      </span>
    </div>
  </section>
</div>
</body>
</html>
```